Visitenkarten-Design für Sonnen-/Fensterschutz
Zielgruppe
KLW GmbH ist eine Firma, die Sonnenschutz und Fensterschutz anbieten.
'Ihr kompetenter Partner in Sachen Sonnenschutz- , Fenster- und Türtechnik. Sie erhalten echtes Handwerk aus dem Mühlviertel zu fairen Preisen.'
Unsere Zielgruppe sind Personen mit Haus, die am Land leben.
Firmenname: KLW GmbH
Slogan: Fenster & Sonnenschutz
Aufgabenstellung
Hier befindet sich das Logodesign: https://dx.qv/t-QwLpo7RbNs
Bitte ein schlichtes Design bereitstellen mit einer Dummy-Person:
Jonas Weidlinger + Telefonnummer + Email
Die finalen Daten bitte erst am Schluss berücksichtigen (für Gewinnerdesign)
Gerne auch hintern + vorne bedruckbar bereitstellen.

```html
<!DOCTYPE html>
<html lang="de">
<head>
<meta charset="utf-8">
<title>KLW GmbH – Visitenkarte</title>
<link rel="stylesheet" href="https://fonts.googleapis.com/css2?family=Open+Sans:wght@400;600;800&family=Montserrat:wght@400;500&display=swap">
<style>
  :root {
    --stage: #555555;
    --card: #ffffff;
    --orange: #f07b1f;
    --red: #e23a24;
    --ink: #555555;
    --ink-soft: #4a4a4a;
    --divider: #f6c9a8;
    --pattern-a: #fdeee3;
    --pattern-b: #fbe3d2;
  }
  * { margin: 0; padding: 0; box-sizing: border-box; }
  html, body { width: 1200px; height: 1200px; overflow: hidden; }
  body { background: var(--stage); position: relative; font-family: "Open Sans", sans-serif; }

  .card {
    position: absolute;
    left: 247px;
    width: 669px;
    height: 432px;
    background: var(--card);
    overflow: hidden;
  }
  .card--front { top: 112px; }
  .card--back { top: 618px; }

  .speed-lines { position: absolute; left: 0; top: 166px; }
  .speed-lines { top: 54px; }

  .brand-mark {
    position: absolute;
    display: flex;
    align-items: center;
    gap: 10px;
    font-family: "Open Sans", sans-serif;
    font-weight: 800;
    color: var(--red);
    white-space: nowrap;
  }
  .brand-mark__square { background: var(--orange); display: block; }
  .brand-mark--header { right: 34px; top: 42px; font-size: 44px; }
  .brand-mark--header .brand-mark__square { width: 26px; height: 26px; }
  .brand-mark--hero { left: 50%; top: 50%; transform: translate(-50%, -50%); font-size: 92px; gap: 18px; }
  .brand-mark--hero .brand-mark__square { width: 54px; height: 54px; }

  .contact {
    position: absolute;
    left: 60px;
    top: 184px;
    font-family: "Montserrat", sans-serif;
    color: var(--ink);
  }
  .contact__company { font-size: 16px; font-weight: 500; color: #777; margin-bottom: 6px; margin-left: 0; }
  .contact__row { display: flex; align-items: flex-start; gap: 6px; font-size: 19px; line-height: 20px; margin-bottom: 14px; }
  .contact__row svg { flex: none; margin-top: 2px; }

  .divider {
    position: absolute;
    left: 356px;
    top: 184px;
    width: 1px;
    height: 140px;
    background: var(--divider);
  }

  .person { position: absolute; left: 384px; width: 260px; top: 232px; text-align: center; color: var(--ink-soft); }
  .person__name { font-size: 23px; font-weight: 400; }
  .person__role { font-size: 17px; font-weight: 600; margin-top: 4px; }

  .footer-band {
    position: absolute;
    left: 0; right: 0;
    top: 400px;
    height: 12px;
    background: linear-gradient(90deg, var(--orange), var(--red));
  }

  .back-pattern {
    position: absolute;
    inset: 0;
    background: linear-gradient(135deg, var(--pattern-a), var(--pattern-b));
  }
</style>
</head>
<body>

  <section class="card card--front" aria-label="Vorderseite">
    <svg class="speed-lines" width="400" height="50" viewBox="0 0 400 50" aria-hidden="true">
      <defs>
        <linearGradient id="line-grad" x1="0" x2="1" y1="0" y2="0">
          <stop offset="0" stop-color="#f07b1f"/>
          <stop offset="1" stop-color="#e23a24"/>
        </linearGradient>
      </defs>
      <rect x="0" y="0" width="370" height="4" fill="url(#line-grad)"/>
      <rect x="0" y="12" width="380" height="6" fill="url(#line-grad)"/>
      <rect x="0" y="25" width="390" height="6" fill="url(#line-grad)"/>
      <rect x="0" y="38" width="400" height="8" fill="url(#line-grad)"/>
    </svg>

    <div class="brand-mark brand-mark--header"><span class="brand-mark__square"></span>KLW GmbH</div>

    <div class="contact">
      <p class="contact__company">KLW GmbH</p>
      <div class="contact__row">
        <svg width="22" height="22" viewBox="0 0 22 22" aria-hidden="true"><path d="M1 2 L21 11 L1 20 L6 11 Z" fill="none" stroke="#e23a24" stroke-width="2.2" stroke-linejoin="round"/></svg>
        <span>Am Weidenfeld 14-16<br>30519 Hannover</span>
      </div>
      <div class="contact__row">
        <svg width="20" height="20" viewBox="0 0 20 20" aria-hidden="true"><path d="M4 1 L8 5 L6 8 C7 11 9 13 12 14 L15 12 L19 16 L16 19 C8 18 2 12 1 4 Z" fill="#e23a24"/></svg>
        <span>+49 151 204 8837</span>
      </div>
      <div class="contact__row">
        <svg width="20" height="18" viewBox="0 0 20 18" aria-hidden="true"><rect x="1" y="4" width="18" height="12" rx="1" fill="#e23a24"/><path d="M1 4 L10 11 L19 4" fill="none" stroke="#fff" stroke-width="1.5"/></svg>
        <span>+49 151 204 8837</span>
      </div>
    </div>

    <div class="divider"></div>

    <div class="person">
      <p class="person__name">Jonas Weidlinger</p>
      <p class="person__role">Geschäftsführer</p>
    </div>

    <div class="footer-band"></div>
  </section>

  <section class="card card--back" aria-label="Rückseite">
    <div class="back-pattern" role="img" aria-label="Dezentes Hintergrundmuster in hellem Pfirsichton"></div>
    <div class="brand-mark brand-mark--hero"><span class="brand-mark__square"></span>KLW GmbH</div>
  </section>

</body>
</html>
```